One page informative flyer for Florist

We are looking for a simple one page flyer. We are a florist who sell flowers, and commemorative t-shirts at graduation ceremonies, and need a flyer that can be given out to students so that they will know what is available on site. Further, we want the flyer to be editable (ie. a word template, or some other program), so that we can change the schools name, and change small bits of the copy easily.

What we are really looking for is a simple template, but we need 4 iterations of the flyer. With each of our two logos, I will need a flyer for t-shirts, and a flyer for flowers. Making 4 total. Please see breakdown below as explanation:

1, Tasselgate Flowers logo - flyer for flowers
2. Tasselgate Flowers logo - flyer for shirts
3. Mortarboard Bloom Co logo - flyer for flowers
4. Mortarboard Bloom Co logo - flyer for shirts

Please see logos for Tasselgate Flowers and Mortarboard Bloom Co attached, as well as a picture of flowers and of the shirts. Feel free to use those images or stock images.

Here is the copy:

Flowers - A variety floral arrangements will be available for purchase at our stand, located conveniently at the graduation ceremony. You can browse our selection & pre-order ahead of time at: www.mortarboardbloomco.example/index,php/test

T-Shirts - Commerative T-Shirts displaying all of the students names will be available for purchase at our stand, located conveniently at the graduation ceremony. You can pre-order ahead of time to guarantee your choice of size at: www.mortarboardbloomco.example/index.php/test

```html
<!DOCTYPE html>
<html lang="en">
<head>
<meta charset="utf-8">
<title>Tasselgate Flowers – Graduation T-Shirts Flyer</title>
<link rel="stylesheet" href="https://fonts.googleapis.com/css2?family=Oswald:wght@500&family=Arimo:wght@400;700&display=swap">
<style>
  :root {
    --paper: #edf1cd;
    --teal: #235863;
    --leaf: #7b9c3b;
    --copy: #2a5a64;
    --link: #c7283c;
    --white: #ffffff;
    --shirt-light: #f1f1f1;
    --shirt-mid: #d4d4d4;
  }
  * { margin: 0; padding: 0; box-sizing: border-box; }
  html, body { width: 851px; height: 1200px; overflow: hidden; }
  body { background: var(--paper); font-family: "Arimo", Arial, sans-serif; }

  .flyer { position: relative; width: 851px; height: 1200px; background: var(--paper); }

  .school-block {
    position: absolute; left: 0; top: 0; width: 263px; height: 377px;
    background: var(--teal);
  }
  .school-name {
    position: absolute; left: 62px; top: 172px;
    color: var(--white); font-weight: 700; font-size: 25px; letter-spacing: 0.5px;
  }
  .header-rule {
    position: absolute; left: 263px; top: 369px; width: 588px; height: 8px;
    background: var(--teal);
  }

  .brand-name {
    position: absolute; right: 42px; top: 42px; text-align: right;
    font-family: "Oswald", "Arial Narrow", sans-serif; font-weight: 500;
    color: var(--leaf); font-size: 104px; line-height: 114px;
  }

  .product-photo {
    position: absolute; left: 211px; top: 422px; width: 430px; height: 356px;
    border: 2px solid var(--teal); border-radius: 16px; overflow: hidden;
    background: radial-gradient(ellipse at 50% 45%, var(--shirt-light) 0%, var(--shirt-mid) 100%);
  }

  .offer-copy {
    position: absolute; left: 79px; top: 826px; width: 700px;
    color: var(--copy); font-size: 28px; line-height: 37px;
  }
  .offer-copy span { display: block; white-space: nowrap; }

  .order-link {
    position: absolute; left: 79px; top: 1058px;
    color: var(--link); font-weight: 700; font-size: 29px;
  }
</style>
</head>
<body>
<main class="flyer">
  <div class="school-block"><p class="school-name">SCHOOL</p></div>
  <div class="header-rule"></div>

  <h1 class="brand-name">Tasselgate<br>Flowers</h1>

  <div class="product-photo" role="img" aria-label="Photo of white commemorative t-shirts, front with school name and logo, back listing the graduating class names"></div>

  <p class="offer-copy">
    <span>T-Shirts - Commerative T-Shirts displaying all of the</span>
    <span>students names will be available for purchase at our</span>
    <span>stand, located conveniently at the graduation cere-</span>
    <span>mony. You can pre-order ahead of time to guaran-</span>
    <span>tee your choice of size at:</span>
  </p>

  <p class="order-link">www.mortarboardbloomco.example</p>
</main>
</body>
</html>
```